Medical group practice

We need a flyer design incorporating the three doctors in the practice, there is a general practitioner, ophthalmologist and an obstetrician & Gynaecologist. see the attached file for the concept. will leave the colour design up to you

Target Market(s)

general public

Industry/Entity Type

Health Care

Colors

Designer to choose colors to be used in the design.

Requirements
Must have
• logos included in attachement

```html
<!DOCTYPE html>
<html lang="en">
<head>
<meta charset="utf-8">
<title>Clearvale Medical – Flyer</title>
<link href="https://fonts.googleapis.com/css2?family=Ubuntu:wght@400;500;700&family=Oswald:wght@500;600&display=swap" rel="stylesheet">
<style>
  :root{
    --backdrop:#000000;
    --paper:#ffffff;
    --cream:#f5ecdc;
    --brand-red:#d0212e;
    --brand-grey:#5e5f63;
    --bar-grey:#6b6b6b;
    --gp-blue:#0a73a8;
    --eye-purple:#7c0a82;
    --obgyn-navy:#0b3b70;
    --accent-yellow:#f6e814;
    --ink:#1e1e1e;
    --hours-green:#0a9a3c;
  }
  *{margin:0;padding:0;box-sizing:border-box}
  html,body{width:1165px;height:1200px;overflow:hidden;background:var(--backdrop)}
  body{position:relative;font-family:"Ubuntu",sans-serif}
  .size-note{position:absolute;left:252px;top:70px;color:#fff;font-family:Arial,sans-serif;font-size:16px}
  .flyer{position:absolute;left:253px;top:93px;width:659px;height:1018px;background:var(--paper);overflow:hidden}

  .header{position:absolute;left:0;top:0;width:659px;height:269px;
    background:linear-gradient(90deg,#f3f6f8 0%,#e9eff2 55%,#dfe8ec 100%)}
  .header-photo{position:absolute;right:0;top:0;width:250px;height:269px;
    background:linear-gradient(100deg,rgba(233,239,242,0) 0%,#cfe3ea 25%,#b9d4df 55%,#9cc1cf 100%)}
  .brand{position:absolute;left:40px;top:108px;display:flex;align-items:center;gap:10px}
  .brand-dot{width:22px;height:22px;border-radius:50%;background:var(--brand-red)}
  .brand-name{font-weight:700;font-size:31px;color:var(--brand-red);letter-spacing:.3px}
  .tagline{position:absolute;left:89px;top:146px;font-size:23px;color:#3a3a3a;letter-spacing:.4px}
  .address-bar{position:absolute;left:40px;top:176px;width:422px;height:19px;background:var(--bar-grey);
    color:#fff;font-family:"Oswald",sans-serif;font-weight:500;font-size:14px;line-height:19px;text-align:center}

  .specialties{position:absolute;left:0;top:269px;width:659px;height:108px;display:flex;gap:2px;background:#fff}
  .specialty{flex:1;display:flex;flex-direction:column;align-items:center;justify-content:center;text-align:center;color:#fff}
  .specialty--gp{background:var(--gp-blue)}
  .specialty--eye{background:var(--eye-purple)}
  .specialty--obgyn{background:var(--obgyn-navy)}
  .specialty-title{color:var(--accent-yellow);font-weight:700;font-size:20px;line-height:19px;margin-bottom:5px}
  .specialty-phone{font-weight:700;font-size:15px;line-height:19px;display:flex;align-items:flex-start;gap:4px}
  .specialty-phone svg{margin-top:2px;flex:none}

  .doctor{position:absolute;left:0;width:659px;background:linear-gradient(180deg,var(--cream) 0%,#fbf8f2 45%,#ffffff 100%)}
  .doctor--gp{top:379px;height:283px}
  .doctor--eye{top:569px;height:192px}
  .doctor--obgyn{top:761px;height:192px}
  .doctor--gp{height:190px}
  .doctor-text{position:absolute;right:160px;text-align:right;color:var(--ink)}
  .doctor-name{font-weight:700;font-size:34px;line-height:40px}
  .doctor--gp .doctor-name{color:var(--gp-blue)}
  .doctor--eye .doctor-name{color:var(--eye-purple)}
  .doctor--obgyn .doctor-name{color:var(--obgyn-navy)}
  .practice-name{font-family:"Oswald",sans-serif;font-weight:500;font-size:30px;line-height:36px;color:#222}
  .doctor-line{font-size:21px;line-height:28px;font-weight:500}
  .doctor-email{display:inline-flex;align-items:center;gap:7px}
  .doctor-mark{position:absolute;left:502px}

  .hours{position:absolute;left:0;top:953px;width:659px;height:65px;background:var(--hours-green);
    text-align:center;color:#fff;font-weight:700;padding-top:9px}
  .hours-title{color:var(--accent-yellow);font-size:19px;line-height:21px}
  .hours-times{font-size:19px;line-height:22px}
</style>
</head>
<body>
  <div class="size-note">Size 5.5x8.5 inches</div>

  <main class="flyer">
    <header class="header">
      <div class="header-photo" role="img" aria-label="Photo of a surgeon wearing a blue cap and surgical mask"></div>
      <div class="brand">
        <span class="brand-dot"></span>
        <span class="brand-name">CLEARVALE MEDICAL</span>
      </div>
      <div class="tagline">YOUR HEALTH IS OUR PRIORITY</div>
      <div class="address-bar">42 Harbour Lane, Eastport, St. Mira. Tel : (555) 410 2280 / 2281</div>
    </header>

    <section class="specialties">
      <div class="specialty specialty--gp">
        <div class="specialty-title">General<br>Practitioner</div>
        <div class="specialty-phone">
          <svg width="15" height="15" viewBox="0 0 16 16"><circle cx="8" cy="8" r="7" fill="none" stroke="#fff" stroke-width="1.5"/><path d="M6 4.5c-1 1-1 5 2 7l1.2-1-1.3-1.6-.8.4c-.6-.8-.8-2-.5-2.8l.9-.1L7 4.4z" fill="#fff"/></svg>
          <span>(555) 320 4417</span>
        </div>
      </div>
      <div class="specialty specialty--eye">
        <div class="specialty-title">Ophthalmologist</div>
        <div class="specialty-phone">
          <svg width="15" height="15" viewBox="0 0 16 16"><circle cx="8" cy="8" r="7" fill="none" stroke="#fff" stroke-width="1.5"/><path d="M6 4.5c-1 1-1 5 2 7l1.2-1-1.3-1.6-.8.4c-.6-.8-.8-2-.5-2.8l.9-.1L7 4.4z" fill="#fff"/></svg>
          <span>(555) 318 9052</span>
        </div>
      </div>
      <div class="specialty specialty--obgyn">
        <div class="specialty-title">Obstetrician/<br>Gynaecologist</div>
        <div class="specialty-phone">
          <svg width="15" height="15" viewBox="0 0 16 16"><circle cx="8" cy="8" r="7" fill="none" stroke="#fff" stroke-width="1.5"/><path d="M6 4.5c-1 1-1 5 2 7l1.2-1-1.3-1.6-.8.4c-.6-.8-.8-2-.5-2.8l.9-.1L7 4.4z" fill="#fff"/></svg>
          <span>(555) 326 7731,<br>(555) 294 6185</span>
        </div>
      </div>
    </section>

    <section class="doctor doctor--gp">
      <div class="doctor-text" style="top:40px">
        <div class="doctor-name">Dr. Calvin Ashford</div>
        <div class="doctor-line">MD, General Practitioner</div>
        <div class="doctor-line doctor-email">
          <svg width="24" height="16" viewBox="0 0 24 16"><rect width="24" height="16" fill="var(--gp-blue)"/><path d="M1 1l11 8 11-8M1 15l8-7M23 15l-8-7" stroke="#fff" stroke-width="1.5" fill="none"/></svg>
          calvin.ashford.clinic@mail.com
        </div>
      </div>
      <svg class="doctor-mark" style="top:42px" width="100" height="100" viewBox="0 0 100 100" aria-hidden="true"><rect x="10" y="10" width="80" height="80" rx="10" fill="var(--gp-blue)"/></svg>
    </section>

    <section class="doctor doctor--eye">
      <div class="doctor-text" style="top:30px">
        <div class="practice-name">Bright Sight Vision Services</div>
        <div class="doctor-name">Dr. Lucinda R. Navarro</div>
        <div class="doctor-line">MD, Surgeon Ophthalmologist</div>
        <div class="doctor-line doctor-email">
          <svg width="24" height="16" viewBox="0 0 24 16"><rect width="24" height="16" fill="var(--eye-purple)"/><path d="M1 1l11 8 11-8M1 15l8-7M23 15l-8-7" stroke="#fff" stroke-width="1.5" fill="none"/></svg>
          lucy.eyedoc@mail.com
        </div>
      </div>
      <svg class="doctor-mark" style="top:36px" width="100" height="100" viewBox="0 0 100 100" aria-hidden="true"><circle cx="50" cy="50" r="38" fill="var(--eye-purple)"/></svg>
    </section>

    <section class="doctor doctor--obgyn">
      <div class="doctor-text" style="top:34px">
        <div class="doctor-name">Dr. Devon Marlowe</div>
        <div class="doctor-line">BMedSci, MBBS, DM (O&amp;G), FACOG</div>
        <div class="doctor-line">Obstetrician &amp; Gynaecologist</div>
        <div class="doctor-line doctor-email">
          <svg width="24" height="16" viewBox="0 0 24 16"><rect width="24" height="16" fill="var(--obgyn-navy)"/><path d="M1 1l11 8 11-8M1 15l8-7M23 15l-8-7" stroke="#fff" stroke-width="1.5" fill="none"/></svg>
          docmarlowe@mail.com
        </div>
      </div>
      <svg class="doctor-mark" style="top:44px" width="100" height="100" viewBox="0 0 100 100" aria-hidden="true"><circle cx="50" cy="50" r="40" fill="var(--obgyn-navy)"/></svg>
    </section>

    <footer class="hours">
      <div class="hours-title">OPENING HOURS :</div>
      <div class="hours-times">Monday - Fridays : 9am - 6pm • &nbsp;Saturdays : 10am - 5pm</div>
    </footer>
  </main>
</body>
</html>
```